Design a modern, classy & professional business card for an online real estate agency, specializing in medium-luxury properties in Thailand and later in Singapore and UK.

Possible design ideas so far: (not essential)

- curved corner(s) to the card, white on front & turquoise on back or visa versa.

- front of card - clear and simple, company name in metallic grey/monochrome, logo graphic & company name on front in spot UV or embossed/debossed effect.

- back of card - large, close-cropped, 'ghost' patterns of the C-shaped curves of logo, or company name repeated on back of card in spot UV.

Target Market(s)

- young to middle-aged professionals mainly (but ideally should design should suit all)

- UK, US,EU,AUS & ASIAN mainly (but ideally should design should suit all countries)

Industry/Entity Type

Real Estate

Requirements
Must have
• THEME:
- Luxurious & Modern
- Clean & striking
- Unique & creative

INFO:
- Logo & company name on front
- Contact details on back:

Tobias Hennlund
Managing Director

www.velmontestates.asia
www.velmontestates.co.uk

Tel: 083-274-6159
email: tobias@velmontestates.asia

(contact details can be displayed in any order as suites design.)

Nice to have
• - curved corner(s) to the card, white on front & turquoise on back or visa versa.

Should not have
• - No generic images of properties, palm trees/coconut trees etc.

- No other other bold colors, except for main turquoise, grey, metallic white & black theme.

- No obvious business card templates

```html
<!DOCTYPE html>
<html lang="en">
<head>
<meta charset="utf-8">
<title>Velmont Estates — Business Card</title>
<link rel="stylesheet" href="https://fonts.googleapis.com/css2?family=Cormorant+Garamond:wght@500&family=Noto+Sans&family=Tinos&family=Arimo&display=swap">
<style>
  :root {
    --stage-glow: #3b5894;
    --stage-mid: #1b2740;
    --stage-edge: #0a0d16;
    --turquoise: #6fdad4;
    --turquoise-deep: #16c3bf;
    --turquoise-pale: #a9ece9;
    --card-grey: #aba8a7;
    --wordmark-grey: #727272;
    --ink: #1e0f0f;
    --rule: #4a4a4a;
  }
  * { margin: 0; padding: 0; box-sizing: border-box; }
  html, body { width: 1200px; height: 889px; overflow: hidden; }
  body {
    position: relative;
    background: radial-gradient(ellipse 620px 520px at 640px 430px, var(--stage-glow) 0%, var(--stage-mid) 55%, var(--stage-edge) 100%);
  }
  .card {
    position: absolute;
    border-radius: 66px;
    overflow: hidden;
  }
  .card-bg { position: absolute; inset: 0; width: 100%; height: 100%; }
  .card--front { left: 85px; top: 40px; width: 708px; height: 403px; background: var(--turquoise); }
  .card--back { left: 427px; top: 425px; width: 706px; height: 405px; background: var(--card-grey); }

  .brand { position: absolute; display: flex; align-items: center; }
  .brand-square { background: var(--turquoise-deep); flex: none; }
  .brand-name {
    font-family: "Cormorant Garamond", Georgia, serif;
    font-weight: 500;
    color: var(--wordmark-grey);
    line-height: 1;
  }
  .brand-name .word-main { display: block; }
  .brand-name .word-sub { display: block; text-transform: uppercase; }

  .card--front .brand { left: 143px; top: 142px; }
  .card--front .brand-square { width: 119px; height: 119px; margin-right: 14px; }
  .card--front .word-main { font-size: 88px; letter-spacing: -1px; }
  .card--front .word-sub { font-size: 30px; letter-spacing: 5px; margin-top: -6px; padding-left: 4px; }

  .card--back .brand { left: 334px; top: 35px; }
  .card--back .brand-square { width: 90px; height: 90px; margin-right: 10px; }
  .card--back .word-main { font-size: 66px; letter-spacing: -1px; }
  .card--back .word-sub { font-size: 22px; letter-spacing: 4px; margin-top: -5px; padding-left: 3px; }

  .holder { position: absolute; left: 0; width: 100%; top: 186px; text-align: center; color: var(--ink); }
  .holder-name { font-family: "Noto Sans", Verdana, sans-serif; font-size: 34px; letter-spacing: 1px; padding-left: 8px; }
  .holder-role { font-family: "Tinos", "Times New Roman", serif; font-size: 26px; margin-top: -4px; }

  .contact {
    position: absolute; left: 60px; top: 310px; width: 586px;
    border-top: 1px solid var(--rule); border-bottom: 1px solid var(--rule);
    padding: 8px 0 6px 3px;
    display: flex; justify-content: space-between;
    font-family: "Arimo", Arial, sans-serif; font-size: 18px; line-height: 23px; color: #111;
  }
  .contact-web { padding-right: 2px; }
  .label-tel { display: inline-block; width: 48px; }
</style>
</head>
<body>
  <section class="card card--front" aria-label="Card front">
    <svg class="card-bg" viewBox="0 0 708 403" aria-hidden="true">
      <polygon points="320,0 708,0 708,142" fill="#ffffff" opacity="0.22"/>
      <polygon points="470,0 708,0 708,70" fill="#ffffff" opacity="0.2"/>
      <polygon points="560,0 708,0 708,30" fill="var(--turquoise-pale)" opacity="0.5"/>
      <polygon points="0,262 300,403 0,403" fill="#ffffff" opacity="0.22"/>
      <polygon points="0,300 170,403 0,403" fill="#e8f4f4" opacity="0.35"/>
    </svg>
    <div class="brand">
      <div class="brand-square"></div>
      <div class="brand-name"><span class="word-main">Velmont</span><span class="word-sub">Estates</span></div>
    </div>
  </section>

  <section class="card card--back" aria-label="Card back">
    <svg class="card-bg" viewBox="0 0 706 405" aria-hidden="true">
      <defs>
        <linearGradient id="back-tint" x1="1" y1="0" x2="0" y2="0.4">
          <stop offset="0" stop-color="#8fe9ea"/>
          <stop offset="0.6" stop-color="#b5d9d9"/>
          <stop offset="1" stop-color="#aba8a7" stop-opacity="0"/>
        </linearGradient>
      </defs>
      <polygon points="40,0 706,0 706,165 360,70" fill="url(#back-tint)" opacity="0.85"/>
      <polygon points="0,30 706,150 706,175 0,60" fill="#ffffff" opacity="0.08"/>
    </svg>
    <div class="brand">
      <div class="brand-square"></div>
      <div class="brand-name"><span class="word-main">Velmont</span><span class="word-sub">Estates</span></div>
    </div>
    <div class="holder">
      <p class="holder-name">Tobias Hennlund</p>
      <p class="holder-role">Managing Director</p>
    </div>
    <div class="contact">
      <div class="contact-direct">
        <p><span class="label-tel">Tel</span>: 083-274-6159</p>
        <p>email : tobias@velmontestates.asia</p>
      </div>
      <div class="contact-web">
        <p>www.velmontestates.asia</p>
        <p>www.velmontestates.co.uk</p>
      </div>
    </div>
  </section>
</body>
</html>
```